FinTech company looking to revamp and expand client-facing interface for our financial models

Pellworth Engines currently has a very simple website that allows clients to interact with our financial models. We are looking to completely redesign the current site and add several extra pages to provide extra functionality. We want the design to have a modern, slick feel, that will work on both a desktop or a tablet. It should be straightforward for clients to move between different pages at any time, and clear from the layout how to interact with the more advanced features. We have included screenshots of existing pages in the attached design brief, as well as sketches of the functionality required by the new pages, but can't provide a direct link to the current site.
Target Market(s)
Professional investors that will be paying to access the interface
Industry/Entity Type
Finance
Number of Pages Required
4 page
Colors
Designer to choose colors to be used in the design.
Look and feel
Each slider illustrates characteristics of the customer's brand and the style your logo design should communicate.

```html
<!DOCTYPE html>
<html lang="en">
<head>
<meta charset="utf-8">
<title>Pellworth Engines – Sensitivities</title>
<link href="https://fonts.googleapis.com/css2?family=Open+Sans:wght@400;600;700&display=swap" rel="stylesheet">
<style>
  :root {
    --teal: #2fae96;
    --teal-soft: #e3f2ee;
    --ink: #1a1a1a;
    --text: #111111;
    --band: #efefef;
    --tab-hover: #f3f3f3;
    --line: #e4e4e4;
    --white: #ffffff;
    --filter-grey: #d6d6d6;
    --navy: #13305a;
  }
  * { box-sizing: border-box; margin: 0; padding: 0; }
  html, body { width: 1200px; height: 678px; overflow: hidden; }
  body {
    font-family: "Open Sans", Arial, sans-serif;
    color: var(--text);
    background: linear-gradient(180deg, #e2e2e2 143px, #f1f1f1 420px, #fafafa 678px);
    position: relative;
  }
  .top-bar {
    position: absolute; left: 0; top: 0; width: 1200px; height: 55px;
    background: var(--white);
    box-shadow: 0 3px 8px rgba(0,0,0,0.12);
    z-index: 3;
  }
  .brand {
    position: absolute; left: 66px; top: 0; line-height: 55px;
    font-weight: 700; font-size: 17px; letter-spacing: 0.2px;
  }
  .horizon { position: absolute; top: 0; height: 55px; display: flex; left: 180px; }
  .horizon a, .main-nav a {
    display: flex; align-items: center; justify-content: center;
    height: 55px; text-decoration: none; color: var(--text);
    font-weight: 700; font-size: 13px; border-right: 1px solid var(--line);
  }
  .horizon a { width: 83px; }
  .horizon a.active, .main-nav a.active { background: var(--teal); color: var(--white); }
  .main-nav { position: absolute; left: 555px; top: 0; display: flex; border-left: 1px solid var(--line); }
  .main-nav a { gap: 8px; font-size: 12.5px; }
  .main-nav svg { width: 22px; height: 22px; }
  .nav-models { width: 129px; }
  .nav-sens { width: 164px; }
  .nav-port { width: 148px; }
  .nav-back { width: 139px; }

  .tab-band {
    position: absolute; left: 0; top: 55px; width: 1200px; height: 88px;
    background: var(--band);
  }
  .sub-tab {
    position: absolute; display: flex; align-items: center; justify-content: center;
    background: var(--white); font-weight: 700; font-size: 12.5px;
    border-radius: 4px 4px 0 0; color: var(--text);
  }
  .sub-tab.plain { background: transparent; }
  .sub-tab.hover { background: var(--tab-hover); box-shadow: 0 -1px 3px rgba(0,0,0,0.05); }
  .tab-more {
    position: absolute; left: 1098px; top: 111px; width: 37px; height: 32px;
    background: var(--white); border-radius: 4px 4px 0 0;
    display: flex; align-items: center; justify-content: center;
  }
  .tab-add { position: absolute; left: 1143px; top: 112px; width: 30px; height: 30px; }

  .export {
    position: absolute; left: 1084px; top: 183px; display: flex; align-items: center; gap: 7px;
    color: var(--teal); font-weight: 700; font-size: 15.5px;
  }

  .filters {
    position: absolute; left: 0; top: 295px; width: 46px; height: 231px;
    background: var(--filter-grey); border-radius: 0 5px 5px 0;
  }
  .filters span {
    position: absolute; left: 50%; top: 50%;
    transform: translate(-50%, -50%) rotate(-90deg);
    font-weight: 700; font-size: 14px; letter-spacing: 1px;
  }
  .filters-toggle { position: absolute; left: 33px; top: 398px; width: 25px; height: 25px; }

  .sens-table {
    position: absolute; left: 97px; top: 217px; width: 1071px;
    border-collapse: separate; border-spacing: 0;
    background: var(--white); border-radius: 6px; overflow: hidden;
    box-shadow: 0 2px 10px rgba(0,0,0,0.1);
    table-layout: fixed;
  }
  .sens-table th {
    height: 65px; font-size: 15.5px; font-weight: 600; color: var(--white);
    border-right: 1px solid rgba(255,255,255,0.18);
  }
  .sens-table th.key { background: var(--ink); border-right-color: #3a3a3a; }
  .sens-table th.stat { background: var(--teal); }
  .sens-table th.sortable svg { margin-left: 4px; vertical-align: middle; }
  .sens-table td {
    height: 63px; text-align: center; font-size: 15.5px;
    border-right: 1px solid var(--line);
  }
  .sens-table td:last-child, .sens-table th:last-child { border-right: none; }
  .sens-table tbody tr:nth-child(even) td { background: var(--teal-soft); }
  .sens-table td.num { text-align: left; padding-left: 28px; }
</style>
</head>
<body>
  <header class="top-bar">
    <div class="brand">PELLQ</div>
    <nav class="horizon">
      <a class="active">250D</a>
      <a>83D</a>
      <a>42D</a>
    </nav>
    <nav class="main-nav">
      <a class="nav-models">
        <svg viewBox="0 0 24 24"><path d="M2 12 L12 3 L22 12 H19 V21 H14 V15 H10 V21 H5 V12 Z" fill="#111"/></svg>MODELS</a>
      <a class="nav-sens active">
        <svg viewBox="0 0 24 24" fill="none" stroke="#fff" stroke-width="1.6"><circle cx="12" cy="12" r="4"/><circle cx="12" cy="12" r="8" stroke-dasharray="2.5 2"/><path d="M12 1v3M12 20v3M1 12h3M20 12h3M4.2 4.2l2 2M17.8 17.8l2 2M4.2 19.8l2-2M17.8 6.2l2-2"/></svg>SENSITIVITIES</a>
      <a class="nav-port">
        <svg viewBox="0 0 24 24" fill="none" stroke="#111" stroke-width="1.8"><circle cx="6.5" cy="6.5" r="4"/><circle cx="17.5" cy="6.5" r="4"/><circle cx="6.5" cy="17.5" r="4"/><circle cx="17.5" cy="17.5" r="4"/></svg>PORTFOLIO</a>
      <a class="nav-back">
        <svg viewBox="0 0 24 24" fill="none" stroke="#111" stroke-width="1.8"><rect x="2" y="3" width="20" height="18"/><path d="M5 17 L9 11 L13 14 L19 7"/></svg>BACKTEST</a>
    </nav>
  </header>

  <div class="tab-band"></div>
  <div class="sub-tab plain" style="left:90px;top:111px;width:138px;height:32px;">EQUITIES</div>
  <div class="sub-tab" style="left:212px;top:111px;width:143px;height:32px;">ETFS</div>
  <div class="sub-tab" style="left:360px;top:102px;width:143px;height:41px;">PAIRS</div>
  <div class="sub-tab hover" style="left:508px;top:92px;width:143px;height:51px;">ETF PAIRS</div>
  <div class="sub-tab" style="left:655px;top:102px;width:143px;height:41px;">FACTORS</div>
  <div class="sub-tab" style="left:803px;top:111px;width:143px;height:32px;">NEW TAB TITLE #1</div>
  <div class="sub-tab" style="left:951px;top:111px;width:143px;height:32px;">NEW TAB TITLE #2</div>
  <div class="tab-more">
    <svg width="14" height="18" viewBox="0 0 14 18"><path d="M3 2 L11 9 L3 16" fill="none" stroke="#666" stroke-width="3"/></svg>
  </div>
  <svg class="tab-add" viewBox="0 0 30 30"><circle cx="15" cy="15" r="11" fill="none" stroke="#666" stroke-width="1.8"/><path d="M15 9v12M9 15h12" stroke="#666" stroke-width="1.8"/></svg>

  <div class="export">
    <svg width="24" height="22" viewBox="0 0 24 22" fill="none" stroke="#2fae96" stroke-width="2"><path d="M10 5 H3 V20 H18 V13"/><path d="M8 15 C9 9 13 6 20 6"/><path d="M16 2 L21 6 L16 10"/></svg>
    Export
  </div>

  <div class="filters"><span>FILTERS</span></div>
  <svg class="filters-toggle" viewBox="0 0 25 25"><circle cx="12.5" cy="12.5" r="11.5" fill="var(--navy)" stroke="#fff" stroke-width="1.5"/><path d="M7 12.5h10M13 8l4.5 4.5L13 17" fill="none" stroke="#fff" stroke-width="2"/></svg>

  <table class="sens-table">
    <colgroup>
      <col style="width:139px"><col style="width:92px"><col style="width:176px">
      <col style="width:83px"><col style="width:83px"><col style="width:83px"><col style="width:83px">
      <col style="width:83px"><col style="width:83px"><col style="width:83px"><col style="width:83px">
    </colgroup>
    <thead>
      <tr>
        <th class="key">Factor</th>
        <th class="key sortable">ID<svg width="10" height="7" viewBox="0 0 10 7"><path d="M1 1l4 4 4-4" fill="none" stroke="#fff" stroke-width="1.8"/></svg></th>
        <th class="key">Sector</th>
        <th class="stat">Stat 1</th><th class="stat">Stat 2</th><th class="stat">Stat 3</th><th class="stat">Stat 4</th>
        <th class="stat">Stat 5</th><th class="stat">Stat 6</th><th class="stat">Stat 7</th><th class="stat">Stat 8</th>
      </tr>
    </thead>
    <tbody>
      <tr><td>Factor 1</td><td>Model 1</td><td>Materials</td><td class="num">-1.4</td><td class="num">0.1</td><td class="num">-3.1</td><td class="num">0.7</td><td class="num">30.2</td><td class="num">0.9</td><td class="num">-3.1</td><td class="num">0.1</td></tr>
      <tr><td>Factor 2</td><td>Model 2</td><td>Materials</td><td class="num">2.8</td><td class="num">0.1</td><td class="num">6.1</td><td class="num">100</td><td class="num">30.2</td><td class="num">0.9</td><td class="num">6.1</td><td class="num">0.1</td></tr>
      <tr><td>Factor 3</td><td>Model 3</td><td>Materials</td><td class="num">-3.7</td><td class="num">2.7</td><td class="num">-7.2</td><td class="num">100</td><td class="num">30.2</td><td class="num">0.9</td><td class="num">-7.2</td><td class="num">2.7</td></tr>
      <tr><td>Factor 4</td><td>Model 4</td><td>Industrials</td><td class="num">2.8</td><td class="num">0.2</td><td class="num">2.7</td><td class="num">0.5</td><td class="num">32.9</td><td class="num">-0.5</td><td class="num">2.7</td><td class="num">0.2</td></tr>
      <tr><td>Factor 5</td><td>Model 5</td><td>Industrials</td><td class="num">0.8</td><td class="num">0.3</td><td class="num">2.5</td><td class="num">0.5</td><td class="num">32.9</td><td class="num">-0.5</td><td class="num">2.5</td><td class="num">0.3</td></tr>
    </tbody>
  </table>
</body>
</html>
```